New Newspaper Ad Design Project

We need an ad design for a magazine to promote our online courses. We're a beverage digital newspaper and recently we launched a platform dedicated to tasting courses. Now we want to promote them on a magazine.
The ad must be visually coherent with the website www.scuolaluppolo.it
The headline is "Corsi online sulla birra"
A second text is the following
La proposta didattica di Accademia Malto:
- Corso di degustazione
- Master sulle birre acide
- Master sugli abbinamenti
- Master sulle birre luppolate
- Focus mensili sul movimento italiano
- Esercitazioni pratiche di assaggio
A third text is the following (presented like a claim or tagline):
Con le birre in assaggio spedite direttamente a casa
We also need to promote a coupon with this text:
Usa il coupon GUSTOPIU10 per uno sconto di € 10 sul carrello*
(small text) * Coupon valido per tutto il 2022
Attached is another zip file with platform logo (2 versions) named "Logo Accademia Malto", that we expect big in the page
Our magazine logo is inside a third zip file named "Logo per media" (several versions). We expect it in the lowest part of the page with this text:
Una garanzia
Diario del Calice
(Diario del Calice is the text inside the logo).
The ad design must be a mix of images and texts. A4 size (21 x 29,7 cm) with +0,5 cm of bleed area or, if you prefer, a graphic grid of 18 x 26,4 cm.
We need a source file in PSD format.
Target Market(s)
Beer enthusiasts
Industry/Entity Type
Beer
Font styles to use
Other font styles liked:
- Roboto Slab
Look and feel

```html
<!DOCTYPE html>
<html lang="it">
<head>
<meta charset="utf-8">
<title>Corsi online sulla birra – Accademia Malto</title>
<link rel="stylesheet" href="https://fonts.googleapis.com/css2?family=Roboto+Slab:wght@300;400;500;700;800&display=swap">
<style>
  :root {
    --page-bg: #d6d6d6;
    --ad-black: #0a0a0a;
    --amber: #f4b41a;
    --cream: #fbf5dc;
    --red: #e8452c;
    --red-dark: #c9321d;
    --text-light: #f2f2f2;
    --text-dark: #1d1d1d;
    --ticket-yellow: #f7cf4a;
  }
  * { margin: 0; padding: 0; box-sizing: border-box; }
  html, body { width: 1200px; height: 2470px; overflow: hidden; }
  body {
    background: var(--page-bg);
    font-family: "Roboto Slab", serif;
    position: relative;
  }
  .ad-page {
    position: absolute;
    left: 100px;
    top: 527px;
    width: 792px;
    height: 1122px;
    transform: scale(1.2626);
    transform-origin: 0 0;
    overflow: hidden;
    background:
      radial-gradient(circle at 80% 30%, rgba(255,255,255,0.06), transparent 30%),
      radial-gradient(circle at 40% 70%, rgba(255,255,255,0.05), transparent 35%),
      var(--ad-black);
    box-shadow: 0 8px 18px rgba(0,0,0,0.35);
  }
  .brand {
    position: absolute; left: 58px; top: 62px;
    display: flex; align-items: center; gap: 10px;
    color: var(--amber);
    font-weight: 500; font-size: 30px; letter-spacing: 0.5px;
  }
  .brand-square { width: 18px; height: 44px; background: var(--amber); }
  .mug-art {
    position: absolute; left: 85px; top: 195px; width: 150px; height: 180px;
    background: radial-gradient(circle, rgba(180,180,180,0.25), rgba(120,120,120,0.08) 70%);
    border-radius: 12px;
  }
  .headline {
    position: absolute; left: 315px; top: 116px;
    font-weight: 800; font-size: 60px; line-height: 60px;
  }
  .headline .line-amber { color: var(--amber); display: block; }
  .headline .line-cream { color: var(--cream); display: block; }
  .intro {
    position: absolute; left: 317px; top: 262px; width: 418px;
    color: var(--text-light); font-weight: 700; font-size: 19px;
    padding-bottom: 8px; border-bottom: 2px solid #bdbdbd;
  }
  .course-list { position: absolute; left: 316px; top: 335px; list-style: none; }
  .course-item {
    display: flex; align-items: center; height: 54px; margin-bottom: 16px;
    color: var(--text-light); font-size: 18px; font-weight: 400;
  }
  .course-icon {
    width: 54px; height: 54px; border-radius: 50%;
    background: var(--red); border: 2px solid #f3f3f3;
    margin-right: 9px; flex-shrink: 0;
  }
  .tagline-band {
    position: absolute; left: 405px; top: 785px; width: 387px; height: 52px;
    background: var(--cream); padding: 6px 0 0 20px;
    font-size: 17px; line-height: 21px; text-transform: uppercase;
  }
  .tagline-band .accent { color: var(--red); display: block; }
  .tagline-band .strong { color: var(--text-dark); display: block; font-weight: 500; }
  .truck-art {
    position: absolute; left: 315px; top: 778px; width: 98px; height: 70px;
    background: linear-gradient(90deg, var(--red) 0 34%, var(--ticket-yellow) 34% 100%);
    border-radius: 8px;
  }
  .photo {
    position: absolute; left: 0; top: 500px; width: 400px; height: 622px;
    background:
      radial-gradient(ellipse at 58% 60%, rgba(230,170,70,0.55), transparent 30%),
      linear-gradient(160deg, #4a2c1c 0%, #b57b5d 40%, #3a5c8c 85%, #1f4fb0 100%);
  }
  .coupon {
    position: absolute; left: 405px; top: 868px; width: 300px; height: 135px;
    background: var(--red);
    border-radius: 6px;
  }
  .coupon-inner {
    position: absolute; left: 30px; top: 10px; width: 240px; height: 115px;
    background: linear-gradient(160deg, #ffffff 0 60%, var(--ticket-yellow) 60% 100%);
    border-radius: 3px;
  }
  .coupon-side {
    position: absolute; left: 8px; top: 100px;
    transform: rotate(-90deg); transform-origin: 0 0;
    font-size: 11px; color: var(--text-dark); letter-spacing: 0.5px;
  }
  .coupon-rule { position: absolute; left: 34px; top: 10px; width: 1px; height: 95px; background: var(--text-dark); }
  .coupon-code {
    position: absolute; left: 42px; top: 10px;
    border: 1.5px solid var(--text-dark); padding: 1px 8px;
    font-size: 20px; font-weight: 500; color: var(--text-dark);
  }
  .coupon-text { position: absolute; left: 46px; top: 47px; font-size: 15px; color: var(--text-dark); }
  .coupon-value { position: absolute; left: 44px; top: 64px; font-size: 38px; color: var(--text-dark); }
  .coupon-note { position: absolute; left: 120px; top: 92px; font-size: 11px; color: var(--text-dark); }
  .media-mark {
    position: absolute; left: 445px; top: 1028px; width: 290px;
    display: flex; align-items: center; justify-content: flex-end; gap: 8px;
    color: var(--text-light); font-size: 30px; font-weight: 400;
  }
  .media-dot { width: 20px; height: 20px; border-radius: 50%; background: #7bc043; }
  .fine-print {
    position: absolute; right: 57px; top: 1075px;
    color: var(--text-light); font-size: 7px; text-transform: uppercase;
  }
</style>
</head>
<body>
  <main class="ad-page">
    <div class="photo" role="img" aria-label="Foto di una donna che annusa un boccale di birra chiara"></div>

    <div class="brand"><span class="brand-square"></span><span>Accademia Malto</span></div>

    <div class="mug-art" role="img" aria-label="Illustrazione lineare di un boccale di birra con schiuma"></div>

    <h1 class="headline">
      <span class="line-amber">CORSI ONLINE</span>
      <span class="line-cream">SULLA BIRRA</span>
    </h1>

    <p class="intro">La proposta didattica di Accademia Malto:</p>

    <ul class="course-list">
      <li class="course-item"><span class="course-icon" role="img" aria-label="Icona degustazione"></span>Corso di degustazione</li>
      <li class="course-item"><span class="course-icon" role="img" aria-label="Icona birre acide"></span>Master sulle birre acide</li>
      <li class="course-item"><span class="course-icon" role="img" aria-label="Icona abbinamenti"></span>Master sugli abbinamenti</li>
      <li class="course-item"><span class="course-icon" role="img" aria-label="Icona luppolo"></span>Master sulle birre luppolate</li>
      <li class="course-item"><span class="course-icon" role="img" aria-label="Icona focus"></span>Focus mensili sul movimento italiano</li>
      <li class="course-item"><span class="course-icon" role="img" aria-label="Icona assaggio"></span>Esercitazioni pratiche di assaggio</li>
    </ul>

    <div class="tagline-band">
      <span class="accent">Con le birre in assaggio</span>
      <span class="strong">Spedite direttamente a casa</span>
    </div>
    <div class="truck-art" role="img" aria-label="Illustrazione di un furgone per le consegne"></div>

    <div class="coupon">
      <div class="coupon-inner">
        <span class="coupon-side">USA IL COUPON</span>
        <span class="coupon-rule"></span>
        <span class="coupon-code">GUSTOPIU10</span>
        <span class="coupon-text">PER UNO SCONTO DI</span>
        <span class="coupon-value">€10</span>
        <span class="coupon-note">SUL CARRELLO</span>
      </div>
    </div>

    <div class="media-mark"><span class="media-dot"></span><span>Diario del Calice</span></div>
    <p class="fine-print">*Coupon valido per tutto il 2022</p>
  </main>
</body>
</html>
```